RWT Fittings Ltd Business Cards

We need a business card with our business logo. We provide window and door installations on high-rises in west coast British Colombia, Canada.

I would like my business information and details on one side of the card, and the other side the company name with logo

Target Market(s)

General Contractors

Industry/Entity Type

Construction

Contact Information for Business Card

one side i want my company name and logo in the dark theme logo that i provided

Requirements
Must have
• Marco Peltieri, 1-604-555-0193, RWTFittings@mailbox-demo.com, 1407-5194 Linden Row Burnaby BC, V5H 2K9, Owner & Manager

```html
<!DOCTYPE html>
<html lang="en">
<head>
<meta charset="utf-8">
<title>RWT Fittings Ltd – Business Cards</title>
<link href="https://fonts.googleapis.com/css2?family=Open+Sans:wght@400;700&display=swap" rel="stylesheet">
<style>
  :root {
    --backdrop: #232323;
    --card: #161616;
    --brand-blue: #29a8e0;
    --white: #f2f2f2;
  }
  * { box-sizing: border-box; margin: 0; padding: 0; }
  html, body {
    width: 1200px; height: 780px; overflow: hidden;
    background: var(--backdrop);
    font-family: "Open Sans", Arial, sans-serif;
  }
  .canvas { position: relative; width: 1200px; height: 780px; }

  .card {
    position: absolute;
    width: 560px; height: 320px;
    background: var(--card);
    border-radius: 24px;
    border-left: 3px solid var(--brand-blue);
    border-bottom: 3px solid var(--brand-blue);
    box-shadow: 0 14px 30px rgba(0,0,0,.55);
    overflow: hidden;
  }
  .card--front { left: 30px; top: 80px; }
  .card--back { left: 610px; top: 380px; }

  .wordmark { display: flex; align-items: center; gap: 16px; }
  .wordmark__square { background: var(--brand-blue); flex: none; }
  .wordmark__name { color: var(--brand-blue); font-weight: 700; line-height: 1; white-space: nowrap; }

  .card--front .wordmark { position: absolute; inset: 0; justify-content: center; }
  .card--front .wordmark__square { width: 46px; height: 46px; }
  .card--front .wordmark__name { font-size: 46px; }

  .card--back .wordmark { position: absolute; left: 34px; top: 34px; gap: 10px; }
  .card--back .wordmark__square { width: 24px; height: 24px; }
  .card--back .wordmark__name { font-size: 24px; }

  .holder {
    position: absolute; right: 0; top: 34px;
    display: flex; align-items: stretch; gap: 10px;
  }
  .holder__text { text-align: right; padding-top: 2px; }
  .holder__name { color: var(--brand-blue); font-weight: 700; font-size: 21px; text-transform: uppercase; line-height: 1.1; }
  .holder__title { color: var(--white); font-size: 13px; margin-top: 3px; }
  .holder__bar { width: 12px; background: var(--brand-blue); }

  .address {
    position: absolute; left: 34px; top: 118px;
    color: var(--white); font-size: 14px; line-height: 1.45; font-style: normal;
  }
  .contacts {
    position: absolute; left: 34px; bottom: 26px;
    list-style: none; color: var(--white); font-size: 14px;
  }
  .contacts li { display: flex; align-items: center; gap: 8px; line-height: 1.6; }
  .contacts svg { width: 13px; height: 13px; fill: var(--brand-blue); flex: none; }
</style>
</head>
<body>
<main class="canvas">

  <section class="card card--front" aria-label="Card front">
    <div class="wordmark">
      <span class="wordmark__square"></span>
      <span class="wordmark__name">RWT Fittings Ltd</span>
    </div>
  </section>

  <section class="card card--back" aria-label="Card back">
    <div class="wordmark">
      <span class="wordmark__square"></span>
      <span class="wordmark__name">RWT Fittings Ltd</span>
    </div>

    <div class="holder">
      <div class="holder__text">
        <p class="holder__name">Marco Peltieri</p>
        <p class="holder__title">Owner &amp; Manager</p>
      </div>
      <span class="holder__bar"></span>
    </div>

    <address class="address">
      1407-5194 Linden Row<br>
      Burnaby BC, V5H 2K9
    </address>

    <ul class="contacts">
      <li>
        <svg viewBox="0 0 24 24" aria-hidden="true"><path d="M6.6 10.8a15.1 15.1 0 0 0 6.6 6.6l2.2-2.2a1 1 0 0 1 1-.25 11.4 11.4 0 0 0 3.6.57 1 1 0 0 1 1 1V20a1 1 0 0 1-1 1A17 17 0 0 1 3 4a1 1 0 0 1 1-1h3.5a1 1 0 0 1 1 1c0 1.25.2 2.46.57 3.6a1 1 0 0 1-.25 1z"/></svg>
        1-604-555-0193
      </li>
      <li>
        <svg viewBox="0 0 24 24" aria-hidden="true"><path d="M2 5h20v14H2z M2 5l10 8 10-8" fill="none" stroke="#29a8e0" stroke-width="2.4"/><path d="M2 5h20l-10 8z"/></svg>
        RWTFittings@mailbox-demo.com
      </li>
      <li>
        <svg viewBox="0 0 24 24" aria-hidden="true"><circle cx="12" cy="12" r="10" fill="none" stroke="#29a8e0" stroke-width="2.4"/><path d="M2 12h20M12 2c3 3 3 17 0 20M12 2c-3 3-3 17 0 20" fill="none" stroke="#29a8e0" stroke-width="1.8"/></svg>
        www.yourwebsite.com
      </li>
    </ul>
  </section>

</main>
</body>
</html>
```